New business card/stationary for a consulting company

I am looking for a clean and very professional looking business card for my consulting company as well as corresponding stationary. I am uploading our logo. I like simple and powerful for the feel. No graphics but I am open on everything else. Below is my contact information but would like the final to be in a version I can add my employees information into and print. Thank you.

Daniel Whitcombe
dan@ferncliffadvisory.com
2870 North 9th Avenue, Summit Floor, Elm Ridge, Illinois 60531
www.ferncliffadvisory.com

Industry/Entity Type

Consulting

Contact Information for Business Card

Daniel Whitcombe
dan@ferncliffadvisory.com
www.ferncliffadvisory.com

Font styles to use
Serif
Sans Serif

Requirements
Must have
• Our logo and the business card details.
Nice to have
• our website www.ferncliffadvisory.com

```html
<!DOCTYPE html>
<html lang="en">
<head>
<meta charset="utf-8">
<title>Ferncliff Advisory — Business Card</title>
<link rel="stylesheet" href="https://fonts.googleapis.com/css2?family=Questrial&family=Lato:wght@400&display=swap">
<style>
  :root {
    --navy: #03026a;
    --navy-soft: #1e1d8e;
    --ink: #1b1a6a;
    --paper: #ffffff;
    --backdrop: #e9e7e4;
  }
  * { margin: 0; padding: 0; box-sizing: border-box; }
  html, body { width: 1200px; height: 900px; overflow: hidden; }
  body { background: var(--backdrop); position: relative; }

  .card { position: absolute; overflow: hidden; box-shadow: 0 6px 18px rgba(0,0,0,0.12); }

  .card-front {
    left: 78px; top: 34px; width: 588px; height: 364px;
    background: var(--navy); color: var(--paper);
  }
  .front-mark {
    position: absolute; left: 360px; top: 70px; width: 300px; height: 290px;
    background: var(--navy-soft); opacity: 0.9;
  }
  .holder-name {
    position: absolute; left: 34px; top: 48px;
    font-family: "Questrial", sans-serif; font-size: 19px; letter-spacing: 0.06em;
    text-transform: uppercase;
  }
  .address {
    position: absolute; left: 34px; top: 206px;
    font-family: "Lato", sans-serif; font-size: 15.5px; line-height: 22px;
  }
  .contact-list {
    position: absolute; left: 34px; top: 284px; list-style: none;
    font-family: "Lato", sans-serif; font-size: 15.5px; line-height: 22px;
  }
  .contact-list li { display: flex; align-items: center; gap: 5px; }
  .contact-list svg { width: 12px; height: 12px; flex: none; }

  .card-back {
    left: 388px; top: 505px; width: 567px; height: 352px;
    background: var(--paper);
  }
  .brand-square {
    position: absolute; left: 263px; top: 134px; width: 40px; height: 40px;
    background: var(--navy);
  }
  .brand-name {
    position: absolute; left: 0; right: 0; top: 196px; text-align: center;
    font-family: "Questrial", sans-serif; font-size: 24px; letter-spacing: 0.04em;
    color: var(--navy); text-transform: uppercase;
  }
  .back-website {
    position: absolute; left: 0; right: 0; top: 289px; text-align: center;
    font-family: "Lato", sans-serif; font-size: 17px; letter-spacing: 0.02em;
    color: var(--ink);
  }
</style>
</head>
<body>
  <section class="card card-front">
    <div class="front-mark" aria-hidden="true"></div>
    <h1 class="holder-name">Daniel Whitcombe</h1>
    <address class="address">
      2870 North 9th Avenue,<br>
      Summit Floor, Elm Ridge,<br>
      Illinois 60531
    </address>
    <ul class="contact-list">
      <li>
        <svg viewBox="0 0 12 12" aria-hidden="true"><rect x="0.5" y="2" width="11" height="8" fill="#fff"/><path d="M0.5 2 L6 6.5 L11.5 2" fill="none" stroke="#03026a" stroke-width="1"/></svg>
        dan@ferncliffadvisory.com
      </li>
      <li>
        <svg viewBox="0 0 12 12" aria-hidden="true"><circle cx="6" cy="6" r="5.5" fill="#fff"/><path d="M3 4 Q5 3 5 5 Q4 7 6 8 M7 2 Q9 4 8 6" fill="none" stroke="#03026a" stroke-width="1.2"/></svg>
        www.ferncliffadvisory.com
      </li>
    </ul>
  </section>

  <section class="card card-back">
    <div class="brand-square" aria-hidden="true"></div>
    <p class="brand-name">Ferncliff Advisory</p>
    <p class="back-website">www.ferncliffadvisory.com</p>
  </section>
</body>
</html>
```